Web Design For Staffing Company

We need a homepage web design for a technical staffing company.

Please see attached brief for project details.

please make the site modern with bold colors while matching the logo

Be sure to read the attached breif in full beforehand.

Target Market(s)

technical companies looking to hire talent

Industry/Entity Type

Staffing

Number of Pages Required

1 page

Font styles to use
Sans Serif

```html
<!DOCTYPE html>
<html lang="en">
<head>
<meta charset="utf-8">
<title>Northlane Staffing</title>
<link rel="stylesheet" href="https://fonts.googleapis.com/css2?family=Montserrat:wght@400;600;700;800&family=Open+Sans:wght@400;600&display=swap">
<style>
:root{
  --blue:#2f80c6;
  --blue-dark:#1d5f9c;
  --navy:#1b3f6a;
  --ink:#2b2b2b;
  --text:#555;
  --gray:#8a8d91;
  --footer:#2a2b2d;
  --footer-bar:#202123;
  --white:#fff;
}
*{box-sizing:border-box;margin:0;padding:0}
html,body{width:1200px;height:3948px;overflow:hidden}
body{font-family:"Open Sans",Arial,sans-serif;color:var(--text);background:var(--white);position:relative}
h1,h2,h3,h4,.btn,.brand{font-family:"Montserrat",Arial,sans-serif}
.btn{display:inline-block;background:var(--blue);color:var(--white);font-size:14px;font-weight:700;letter-spacing:.5px;border-radius:24px;padding:12px 30px;text-transform:uppercase;text-decoration:none}
.abs{position:absolute}

/* header */
.site-header{left:0;top:0;width:1200px;height:64px;background:var(--white);display:flex;align-items:center;padding:0 50px;z-index:2}
.brand{display:flex;align-items:center;gap:10px;font-size:24px;font-weight:800;color:var(--blue)}
.brand-mark{width:22px;height:22px;background:var(--blue);border-radius:4px}
.main-nav{display:flex;gap:44px;margin-left:auto;margin-right:56px;font-size:15px;color:#444}
.main-nav .active{color:var(--blue);border-bottom:2px solid var(--blue);padding-bottom:2px}
.site-header .btn{padding:10px 30px}

/* hero */
.hero{left:0;top:64px;width:1200px;height:560px;background:linear-gradient(180deg,#6d7072 0%,#8d9092 55%,#a9abac 100%)}
.hero-title{left:0;top:150px;width:1200px;text-align:center;color:var(--white);font-size:34px;font-weight:700;line-height:1.3;letter-spacing:.5px;text-transform:uppercase}
.hero-actions{left:0;top:262px;width:1200px;display:flex;justify-content:center;gap:24px}
.hero-actions .btn{padding:13px 38px}

/* intro */
.intro{left:340px;top:710px;width:520px;text-align:center;font-size:14px;line-height:1.6}

/* feature rows */
.feature-photo{background:linear-gradient(135deg,#b5aca2,#8f7d6e 60%,#d9d3cc)}
.photo-a{left:0;top:880px;width:600px;height:430px}
.photo-b{left:600px;top:1310px;width:600px;height:445px;background:linear-gradient(135deg,#e8edf1,#9fb2c2 55%,#c7b8a6)}
.feature-text{font-size:15px;line-height:1.7}
.text-a{left:655px;top:945px;width:450px}
.actions-a{left:655px;top:1170px;display:flex;gap:22px}
.text-b{left:90px;top:1385px;width:470px}
.actions-b{left:90px;top:1605px;display:flex;gap:22px}
.feature-actions .btn{padding:13px 36px}

/* testimonials */
.section-title{left:0;width:1200px;text-align:center;font-size:40px;font-weight:700;color:var(--ink);letter-spacing:1px}
.t-title{top:1830px}
.avatar{left:535px;top:1900px;width:130px;height:130px;border-radius:50%;background:radial-gradient(circle,#d9c6b4,#8f7f70)}
.t-name{left:0;top:2046px;width:1200px;text-align:center;font-size:18px;color:var(--ink)}
.t-role{left:0;top:2074px;width:1200px;text-align:center;font-size:16px;color:var(--ink)}
.t-quote{left:160px;top:2112px;width:880px;text-align:center;font-size:14px;line-height:1.7}

/* blog */
.blog{left:0;top:2300px;width:1200px;height:660px;background:linear-gradient(180deg,#3d8bd0,#2466a8)}
.blog-title{top:2370px;color:var(--white)}
.card{top:2455px;width:325px;height:495px;background:var(--white)}
.card-1{left:95px}.card-2{left:437px}.card-3{left:779px}
.card-img{width:325px;height:205px;background:linear-gradient(135deg,#9aa7b3,#4b5968)}
.card-2 .card-img{background:linear-gradient(135deg,#c8b49b,#6e5b49)}
.card-3 .card-img{background:linear-gradient(135deg,#b9c4cf,#5b6e80)}
.date{position:absolute;left:16px;top:178px;width:62px;height:64px;background:var(--blue);color:var(--white);text-align:center;font-family:"Montserrat",sans-serif;font-weight:700;line-height:1.1;padding-top:10px}
.date b{display:block;font-size:22px}.date span{font-size:12px}
.card-body{padding:50px 18px 0}
.card h3{font-size:21px;line-height:1.2;color:var(--ink);margin-bottom:10px}
.card p{font-size:12px;line-height:1.5;margin-bottom:8px}
.read{font-family:"Montserrat",sans-serif;font-size:14px;font-weight:700;color:var(--blue)}

/* cta */
.cta{top:3040px;width:500px;height:480px;background:linear-gradient(135deg,#2d5f93,#15355c);color:var(--white);text-align:center}
.cta-1{left:90px}.cta-2{left:612px;background:linear-gradient(135deg,#3673ad,#17406b)}
.cta h2{margin:125px auto 36px;width:300px;font-size:32px;font-weight:700;line-height:1.25;text-transform:uppercase}
.cta .btn{padding:13px 34px}

/* footer */
.site-footer{left:0;top:3600px;width:1200px;height:348px;background:var(--footer);color:#cfd0d1}
.f-col{top:3628px;width:310px}
.f-col h4{font-size:24px;font-weight:600;color:var(--white);margin-bottom:20px}
.f-col p{font-size:14px;line-height:1.6;height:66px}
.f-col .btn{margin-top:22px;padding:12px 34px}
.f1{left:95px}.f2{left:480px}.f3{left:865px}
.f-bar{left:0;top:3900px;width:1200px;height:48px;background:var(--footer-bar);font-size:12px;color:#aaa;text-align:center;line-height:48px}
</style>
</head>
<body>

<header class="site-header abs">
  <div class="brand"><span class="brand-mark"></span>Northlane</div>
  <nav class="main-nav">
    <span class="active">Home</span><span>About</span><span>Job Seekers</span><span>Clients</span><span>Contact</span>
  </nav>
  <a class="btn">Search Jobs</a>
</header>

<section class="hero abs" role="img" aria-label="Row of white office chairs with one blue chair against a grey wall"></section>
<h1 class="hero-title abs">The right people for the right jobs!<br>Bridging the talent gap in technical staffing</h1>
<div class="hero-actions abs"><a class="btn">Hire Talent</a><a class="btn">Get Hired</a></div>

<p class="intro abs">Northlane Staffing is a National Technical Staffing and Recruiting Solutions Provider founded in 2011 focused on matching contract and full-time Engineering and IT professionals with new and exciting employment opportunities!</p>

<div class="feature-photo photo-a abs" role="img" aria-label="Two professionals talking in a bright modern office lounge"></div>
<p class="feature-text text-a abs">Simply said... WE LOVE TO RECRUIT! It's our passion and we take it very seriously! It is not easy for JOB SEEKERS to put their job search efforts and trust in the hands of someone else especially when there are so many Staffing Firms to choose from. So how do you know you are choosing the best Staffing Representation possible?</p>
<div class="feature-actions actions-a abs"><a class="btn">Learn More</a><a class="btn">View Jobs</a></div>

<p class="feature-text text-b abs">Are you responsible for Technical Staffing within your organization? Are you satisfied with your current Supplier(s) overall performance? Does it appear they identify potential Candidate(s) based solely on "buzz-word" searches? Is it evident they just do not grasp the scope and responsibilities of your technical staffing need(s)?</p>
<div class="feature-actions actions-b abs"><a class="btn">Learn More</a><a class="btn">Hire Talent</a></div>
<div class="feature-photo photo-b abs" role="img" aria-label="Colleagues meeting around a table in a sunlit office"></div>

<h2 class="section-title t-title abs">TESTIMONIALS</h2>
<div class="avatar abs" role="img" aria-label="Portrait of the client giving the testimonial"></div>
<div class="t-name abs">Sam R.</div>
<div class="t-role abs">-Electrical Test Engineer in the Automotive Sector:</div>
<p class="t-quote abs">"Dana Hale is an excellent recruiter. He is articulate, honest, has a good nature and is an effective information conduit between his clients and candidates. He gave me the feeling he is there for the big picture desiring to forge a future relationship that will be mutually beneficial to both of us."</p>

<section class="blog abs" role="img" aria-label="Blue tinted photo of a business team"></section>
<h2 class="section-title blog-title abs">BLOG</h2>

<article class="card card-1 abs">
  <div class="card-img" role="img" aria-label="Black and white portrait with a quote"></div>
  <div class="date"><b>19</b><span>JUN</span></div>
  <div class="card-body">
    <h3>Tips for Spotting a U.S. Recession Before It Becomes Official</h3>
    <p>As the U.S. nears a record-long expansion in July, the conversation is increasingly turning to when it will all end.</p>
    <span class="read">READ MORE</span>
  </div>
</article>
<article class="card card-2 abs">
  <div class="card-img" role="img" aria-label="Person writing notes at a desk"></div>
  <div class="date"><b>17</b><span>JUN</span></div>
  <div class="card-body">
    <h3>Ways To Make The Most Of The Hot Job Market</h3>
    <p>This is the tightest labor market I can remember. Unemployment is at a 50-year low and wage growth is at 3.3%.</p>
    <span class="read">READ MORE</span>
  </div>
</article>
<article class="card card-3 abs">
  <div class="card-img" role="img" aria-label="Two people shaking hands over a meeting table"></div>
  <div class="date"><b>06</b><span>JUN</span></div>
  <div class="card-body">
    <h3>Back To Basics: Meeting Employees' Needs To Improve Organizational Performance</h3>
    <p>The benefits of employee satisfaction are well established, so HR professionals and leaders across all industries seek a</p>
    <span class="read">READ MORE</span>
  </div>
</article>

<section class="cta cta-1 abs" role="img" aria-label="Blue tinted photo of hiring managers">
  <h2>Looking for career-minded candidates?</h2>
  <a class="btn">Request Talent</a>
</section>
<section class="cta cta-2 abs" role="img" aria-label="Blue tinted photo of a job seeker">
  <h2>Looking for career opportunities?</h2>
  <a class="btn">Search Jobs</a>
</section>

<footer class="site-footer abs"></footer>
<div class="f-col f1 abs">
  <h4>Get Hired</h4>
  <p>Lorem ipsum dolor sit amet, consectetur adipiscing elit, sed do eiusmod</p>
  <a class="btn">Search Now</a>
</div>
<div class="f-col f2 abs">
  <h4>Hire Talent</h4>
  <p>Lorem ipsum dolor sit amet, consectetur adipiscing elit, sed do eiusmod</p>
  <a class="btn">Start Today</a>
</div>
<div class="f-col f3 abs">
  <h4>Address</h4>
  <p>Northlane Staffing, Inc 42 Harbor Street, Suite 2, Millbrook, MA 01000</p>
  <a class="btn">Contact Us</a>
</div>
<div class="f-bar abs">Copyright © 2020. All Rights Reserved</div>

</body>
</html>
```